Redesign This Psychology Website

We would like a slight redesign of this successful psychology (relationship counselling) website:

www.TheKelvaleClinic.com.au

We are updating the website, and we'd like a slight refresh of the design and style.

Please keep to very similar colours, and use the same logo. We're looking for around 10 page templates, however the main one is the home page.

Keep in mind, this website already converts quite well, so we want a new, fresh design in keeping with this one. Please don't bother designing something too extremely different.

thanks :)

Target Market(s)

couples who are looking for relationship counselling. Men and women, 25 - 70, across Australia

Industry/Entity Type

Psychology

Number of Pages Required

5+ page

Font styles to use
Sans Serif

Colors
87cfc6
b7a5cd
ec1f27
ffffff
cee9f5

Requirements
Must have
• a similar look to the current design, just looking for a slight refresh.
• Search bar
• Areas for lots of photos
• same logo
• lots of content areas
Nice to have
• great content areas, where we can display a lot of content and our areas.
Should not have
• no colors like orange, etc.
• should not have a totally different feel.

```html
<!DOCTYPE html>
<html lang="en">
<head>
<meta charset="utf-8">
<title>Why am I with a Narcissist? – Kelvale Clinic Blog</title>
<link href="https://fonts.googleapis.com/css2?family=Mulish:wght@400;600;700&display=swap" rel="stylesheet">
<style>
:root{
  --teal:#87cfc6;
  --teal-dark:#5fb9ae;
  --lavender:#b7a5cd;
  --red:#ec1f27;
  --sky:#cee9f5;
  --white:#ffffff;
  --ink:#2b2b2b;
  --body:#6b6b6b;
  --line:#e3e3e3;
  --pale:#f4f4f4;
}
*{box-sizing:border-box;margin:0;padding:0}
html,body{width:1200px;height:3644px;overflow:hidden}
body{font-family:"Mulish",Arial,sans-serif;color:var(--body);background:var(--white);position:relative}
a{color:inherit;text-decoration:none}
.wrap{position:absolute;left:130px;width:940px}

/* top utility bar */
.utility-bar{position:absolute;top:0;left:0;width:1200px;height:36px;background:var(--pale);font-size:12px}
.utility-bar .associate{position:absolute;left:130px;top:11px;color:#777}
.utility-links{position:absolute;right:130px;top:0;display:flex;height:36px}
.utility-links a{padding:11px 12px;border-left:1px solid var(--line);color:#777}

/* header */
.site-header{position:absolute;top:36px;left:0;width:1200px;height:122px}
.brand{position:absolute;left:130px;top:26px;display:flex;align-items:center;gap:12px}
.brand-dot{width:46px;height:46px;border-radius:50%;background:var(--red)}
.brand-name{font-size:32px;font-weight:700;color:var(--teal-dark);line-height:1}
.brand-tagline{font-size:12.5px;color:var(--red);margin-top:4px}
.search{position:absolute;left:474px;top:44px;width:258px;height:34px;border:1px solid #d5d5d5;border-radius:3px;display:flex;align-items:center;padding-left:10px;font-size:12px;color:#9a9a9a;gap:8px}
.call{position:absolute;right:130px;top:36px;text-align:right}
.call small{display:block;font-size:15px;color:var(--teal-dark)}
.call strong{display:flex;align-items:center;gap:6px;font-size:24px;color:var(--red);font-weight:600}

/* nav */
.main-nav{position:absolute;top:158px;left:0;width:1200px;height:66px;background:linear-gradient(var(--teal),#74c3b9)}
.main-nav ul{position:absolute;left:130px;width:940px;height:66px;display:flex;list-style:none}
.main-nav li{display:flex;align-items:center;justify-content:center;text-align:center;color:var(--white);font-size:15px;font-weight:600;text-transform:uppercase;line-height:1.15;border-right:1px solid rgba(255,255,255,.45);padding:0 10px}
.main-nav li:last-child{border-right:0}

/* hero */
.hero{position:absolute;top:224px;left:0;width:1200px;height:330px;background:linear-gradient(100deg,#c98a5e 0%,#e7b48d 30%,#f3d9bf 55%,#d9a37d 80%,#a86a47 100%)}
.hero::after{content:"";position:absolute;inset:0;background:rgba(0,0,0,.18)}
.hero h1{position:absolute;left:128px;top:170px;z-index:1;color:var(--white);font-size:38px;font-weight:600;letter-spacing:1px}

/* article */
.article{position:absolute;left:128px;width:604px;font-size:13px;line-height:1.62}
.article h2{color:var(--ink);font-size:28px;font-weight:600}
.article h3{color:var(--red);font-size:25px;font-weight:600;margin-bottom:12px}
.article p{margin-bottom:10px}
.article-photo{float:left;width:298px;height:206px;margin:0 18px 8px 6px;background:linear-gradient(135deg,#cfc3b4,#8f7f70 60%,#5e5248)}
.sacrificial-list{list-style:none}
.sacrificial-list li{margin-bottom:11px;line-height:1.5}

/* sidebar */
.finder{position:absolute;left:768px;top:603px;width:302px;height:357px;background:var(--lavender);padding:22px 28px;color:var(--white)}
.finder h4{text-align:center;font-size:21px;font-weight:600;line-height:1.25}
.finder .rule{width:110px;height:1px;background:rgba(255,255,255,.7);margin:6px auto 16px}
.finder label{display:block;font-size:12px;margin-bottom:4px}
.field{height:32px;background:var(--white);border-radius:2px;margin-bottom:14px;font-size:11px;color:#999;display:flex;align-items:center;justify-content:space-between;padding:0 10px}
.finder .btn{height:38px;background:var(--red);color:var(--white);font-weight:700;font-size:15px;display:flex;align-items:center;justify-content:center;margin-top:4px}

.categories{position:absolute;left:768px;top:984px;width:302px;height:819px;border:1px solid var(--line)}
.categories h4{background:var(--lavender);color:var(--white);font-size:19px;font-weight:600;padding:14px 24px}
.categories ul{list-style:none;padding:14px 24px}
.categories li{font-size:12px;color:#555;height:30.2px;display:flex;align-items:center;gap:10px}
.categories li::before{content:"";width:5px;height:5px;border-right:1.5px solid var(--teal-dark);border-top:1.5px solid var(--teal-dark);transform:rotate(45deg)}

.related{position:absolute;left:768px;width:302px;height:118px;display:flex;background:var(--white);box-shadow:0 1px 5px rgba(0,0,0,.18)}
.related .thumb{width:146px;height:118px;flex:none}
.related .info{padding:14px 12px;font-size:13.5px;color:var(--ink);line-height:1.3}
.related .info span{display:block;margin-top:6px;font-size:11.5px;color:var(--teal-dark)}

/* footer */
.site-footer{position:absolute;top:3268px;left:0;width:1200px;height:304px;background:var(--pale)}
.footer-brand{position:absolute;left:134px;top:80px;display:flex;align-items:center;gap:12px}
.footer-col{position:absolute;top:74px;font-size:12.5px;line-height:2.1}
.footer-col h5{color:var(--teal-dark);font-size:16px;font-weight:700;text-transform:uppercase;margin-bottom:2px}
.socials{display:flex;gap:8px;margin-top:12px}
.socials i{width:30px;height:30px;border-radius:50%;background:var(--teal);display:block}
.copyright{position:absolute;top:3572px;left:0;width:1200px;height:72px;background:#ececec;text-align:center;font-size:12px;line-height:72px;color:#888}
</style>
</head>
<body>

<div class="utility-bar">
  <a class="associate" href="#">Join Our Associate Program »</a>
  <nav class="utility-links"><a href="#">Home</a><a href="#">Cart</a><a href="#">Blog</a><a href="#">Resources</a><a href="#">Contact</a></nav>
</div>

<header class="site-header">
  <div class="brand">
    <span class="brand-dot"></span>
    <div><div class="brand-name">Kelvale Clinic</div><div class="brand-tagline">helping you create loving relationships</div></div>
  </div>
  <div class="search">
    <svg width="13" height="13" viewBox="0 0 13 13"><circle cx="5.5" cy="5.5" r="4.3" fill="none" stroke="#999" stroke-width="1.5"/><line x1="8.6" y1="8.6" x2="12" y2="12" stroke="#999" stroke-width="1.5"/></svg>
    Search here
  </div>
  <div class="call">
    <small>Call Us Now</small>
    <strong><svg width="20" height="20" viewBox="0 0 24 24"><path d="M6.6 10.8a15 15 0 0 0 6.6 6.6l2.2-2.2c.3-.3.7-.4 1-.2 1.1.4 2.3.6 3.6.6.6 0 1 .4 1 1V20c0 .6-.4 1-1 1A17 17 0 0 1 3 4c0-.6.4-1 1-1h3.5c.6 0 1 .4 1 1 0 1.3.2 2.5.6 3.6.1.3 0 .7-.2 1z" fill="#ec1f27"/></svg>1300 555 014</strong>
  </div>
</header>

<nav class="main-nav">
  <ul>
    <li style="width:120px">Counselling<br>Types</li>
    <li style="width:260px">Relationship Counselling<br>Locations</li>
    <li style="width:150px">Sex Therapy<br>Locations</li>
    <li style="width:100px">About Us</li>
    <li style="width:100px">Quizzes</li>
    <li style="width:90px">FAQ's</li>
    <li style="width:120px">Contact</li>
  </ul>
</nav>

<section class="hero" role="img" aria-label="Photo of a smiling couple making a heart shape with their hands">
  <h1>OUR BLOGS</h1>
</section>

<article class="article" style="top:604px">
  <h2>Why am I with a Narcissist?</h2>
  <div style="margin-top:20px">
    <div class="article-photo" role="img" aria-label="Photo of a thoughtful woman with arms crossed"></div>
    <p>You may be wondering why anyone would be masochistic enough to ever get themselves into a relationship with someone who has so many characteristics of a Narcissist and who leaves you feeling so dreadful?</p>
    <p>But the truth is that things start off very differently. The narcissist is an absolute perfect delight right from the first day you start dating: wining, dining and gifts, nothing is too much trouble for him/her; your every whim is his/her desire; he/she is truly the perfect and charming partner.</p>
    <p>Finding yourself in a "whirlwind romance", he/she will appear to be all you have ever wanted in a partner and in a relationship, so much so that it all seems almost "too good to be true", which of course it is.</p>
    <p>At this stage you are his/her "prey", and he/she is an expert at contriving his/her behaviour to impress you, and being sensitive to what you are wanting, until he/she has snared you. He/she has you in his/her sights as his/her next source of Narcissistic supply, so all his/her energies, shows of love, affection and fake empathy are committed to lure you.</p>
  </div>
</article>

<section class="article" style="top:1200px">
  <h3>The transition</h3>
  <p>However this "impress your socks off" stage doesn't last, and once he/she now feels secure in the relationship (this happens most commonly at the 3 major transitions: when you move in together, when you get married, or when you start having children) there is now no longer a need for making an effort.</p>
  <p>Without realizing it, you are now owned by him/her; you have crossed over into his/her self-definition boundary. With this transition comes the expectation that you are now an extension of him/her.</p>
  <p>This dumbfounding change can be made almost overnight, or at a more gradual pace, but change it does.</p>
</section>

<section class="article" style="top:1496px">
  <h3>The "Bubble"</h3>
  <p>One man described that for him it felt like he and his wife were in a big bubble that he had created as his reality. His wife had freedom, and all was happy, as long as she stayed in the bubble. "There was room to move about so the illusion of freedom seemed real to her. But when she expressed an idea of her own, or any feelings, it was like she was stepping out of his bubble and stepping into her own. But he did not want her out there. He feared being alone with himself. He feared being with his feelings. So he tried to pull her back into his bubble, or worse, injure her so she could never leave, or worse yet, disorient her so she can never find her way out." Whatever control measure or verbal abuse it took, getting her back inside the bubble where he could feel safe again was his primary objective.</p>
  <p>The Narcissist usually feels a great and strong love for his/her partner, but this is in essence a control connection rather than real love. There is no regard for his/her individuality, no empathy or understanding, and usually an angry assault or the silent treatment, every time he/she shows any signs of separateness.</p>
  <p>This leaves you feeling shunned, negated, unseen, unheard, trivialised, and, as a result, also very confused, sad, and often outraged that you have been so invaded or negated, every time you express your individuality.</p>
</section>

<section class="article" style="top:1982px">
  <h3>How did you become a willing victim? Why you?</h3>
  <p>If you find yourself in a relationship with a Narcissist, at some stage you might wonder why you? What does this say about you, your tolerance for pain and your sanity?</p>
  <p>It is true that there is a particular kind of person that finds themself with a Narcissist, at least often well beyond the first indication that there is an underlying nastiness in him.</p>
  <p>The kind of person who seems to unwittingly attract a Narcissist is someone who has what I call a "Sacrificial Self", (which has also been referred to as Co-dependent or compliant or a deflated false self). This means you may have a tendency to unnecessarily attribute blame to yourself in situations when you haven't done anything wrong.</p>
  <p>In Transactional Analysis terms, a Narcissist's underlying Life position is I'm Ok, You're Not OK, whereas a Sacrificial's underlying Life Position is I'm Not OK, You're OK.</p>
</section>

<section class="article" style="top:2340px">
  <h3>How Can I tell if I am a Sacrificial Self?</h3>
  <p>Here again, it is important to understand that there are varying degrees of this kind of Self, as there are with a Narcissistic self.</p>
  <p>A Sacrificial person is characterised by:</p>
  <ol class="sacrificial-list" style="margin-top:26px">
    <li>1. A deflated False self</li>
    <li>2. Your feelings are often numbed, and you are not always aware of them in the moment</li>
    <li>3. You experience a lack of awareness of your own needs.</li>
    <li>4. You also are not good at knowing what your real wants are.</li>
    <li>5. You often feel guilt and shame for not being able to meet people's needs</li>
    <li>6. Your loved ones withdrawing their love, or threatening to withdraw it, triggers a lot of anxiety in you</li>
    <li>7. You are often not truly in touch with your own deeper truth</li>
    <li>8. You can often prefer to live in a fantasy where you believe your partner truly loves you, even though much of the evidence can show you the contrary</li>
    <li>9. You have experienced poor self esteem over your life</li>
    <li>10. You are not always able to see where your boundaries should and shouldn't be</li>
    <li>11. You are not often able to assertively stand up to those you love</li>
    <li>12. You can at times feel a vague sense of depression and emptiness</li>
    <li>13. You can lack a sense of a healthy entitlement in your relationships</li>
    <li>14. You can often feel frustrated and dissatisfied with your life</li>
    <li>15. There are times when you feel your life has no meaning</li>
    <li>16. You have an underlying belief that I must sacrifice myself to survive in a relationship</li>
    <li>17. In a relationship, you may be responsive and reactive to your partner, rather than proactive</li>
    <li>18. You excessively blame yourself in your relationship</li>
    <li>19. You often have the underlying sense that if something is going right for you at the moment, it probably won't last.</li>
    <li>20. You tend to take more than your fair share of responsibility in a relationship, to make it better and improve it.</li>
  </ol>
</section>

<aside class="finder">
  <h4>Find Our Psychologist<br>Near You</h4>
  <div class="rule"></div>
  <label>Type of Counselling</label>
  <div class="field">Select <svg width="10" height="6" viewBox="0 0 10 6"><path d="M1 1l4 4 4-4" fill="none" stroke="#888" stroke-width="1.4"/></svg></div>
  <label>Location</label>
  <div class="field"></div>
  <label>Postcode</label>
  <div class="field"></div>
  <div class="btn">SEARCH</div>
</aside>

<aside class="categories">
  <h4>Blogs Categories</h4>
  <ul>
    <li>Affairs</li><li>Assertiveness</li><li>Attachment</li><li>Break up</li><li>Communication</li>
    <li>Compatibility</li><li>Controlling</li><li>Couples counselling</li><li>Empathy</li><li>Enneagram</li>
    <li>Financial stress</li><li>Individual counselling for relationships</li><li>Infertility</li><li>Intimacy</li><li>Marriage counselling</li>
    <li>Narcissism</li><li>Personal growth</li><li>Personality</li><li>psychological wellbeing</li><li>Psychologist Interviews</li>
    <li>Relationship counselling</li><li>Relationship happiness</li><li>Relationship problems</li><li>Singles</li><li>Uncategorized</li>
  </ul>
</aside>

<a class="related" style="top:1890px"><div class="thumb" role="img" aria-label="Photo of a couple sitting apart" style="background:linear-gradient(135deg,#d8cfc4,#8e8379)"></div><div class="info">What can I do if I'm living with a Narcissist?<span>Read More</span></div></a>
<a class="related" style="top:2017px"><div class="thumb" role="img" aria-label="Photo of a man holding his head" style="background:linear-gradient(135deg,#6e6a66,#2f2d2b)"></div><div class="info">Are You Living With a Steamroller?<span>Read More</span></div></a>
<a class="related" style="top:2143px"><div class="thumb" role="img" aria-label="Photo of an upset couple" style="background:linear-gradient(135deg,#b7aaa0,#5c524b)"></div><div class="info">Did Your Relationship Start on Rocky Ground?<span>Read More</span></div></a>
<a class="related" style="top:2289px"><div class="thumb" role="img" aria-label="Photo of a thoughtful woman" style="background:linear-gradient(135deg,#e2d6c8,#a69280)"></div><div class="info">Why am I with a Narcissist?<span>Read More</span></div></a>
<a class="related" style="top:2418px"><div class="thumb" role="img" aria-label="Photo of a couple talking on a sofa" style="background:linear-gradient(135deg,#cdd5dc,#7a8590)"></div><div class="info">Letter for a Partner Doubtful About Relationship Counselling<span>Read More</span></div></a>
<a class="related" style="top:2544px"><div class="thumb" role="img" aria-label="Photo of a couple arm wrestling" style="background:linear-gradient(135deg,#e6c7b8,#b05a4a)"></div><div class="info">What Are You Like In a Relationship?<span>Read More</span></div></a>
<a class="related" style="top:2673px"><div class="thumb" role="img" aria-label="Photo of a worried man" style="background:linear-gradient(135deg,#a38c78,#4b3a2e)"></div><div class="info">How Do I Know If I'm With A Narcissist?<span>Read More</span></div></a>
<a class="related" style="top:2799px"><div class="thumb" role="img" aria-label="Photo of a couple standing back to back" style="background:linear-gradient(135deg,#ead9c6,#a88a6d)"></div><div class="info">Do You Wonder Why You and Your Partner Are Together?<span>Read More</span></div></a>
<a class="related" style="top:2928px"><div class="thumb" role="img" aria-label="Photo of a couple at a dinner table" style="background:linear-gradient(135deg,#d9c9b8,#7d6a58)"></div><div class="info">Is Your Pursuit of Success Sabotaging Your Relationships That Matter Most?<span>Read More</span></div></a>

<footer class="site-footer">
  <div class="footer-brand">
    <span class="brand-dot"></span>
    <div><div class="brand-name">Kelvale Clinic</div><div class="brand-tagline">helping you create loving relationships</div></div>
  </div>
  <div class="footer-col" style="left:452px">
    <h5>Quick Links</h5>
    Home<br>About Us<br>Our Blogs<br>Shop Cart<br>Contact Us
  </div>
  <div class="footer-col" style="left:620px">
    <h5>Resources</h5>
    Counselling Type<br>Sex Therapy<br>Quizzes<br>FAQ<br>Relationship Counselling
  </div>
  <div class="footer-col" style="left:824px">
    <h5>Contact Us</h5>
    42 Harbour Lane Suite 3<br>1300 555 014<br>Email: info@kelvaleclinic.com.au
    <div class="socials"><i></i><i></i><i></i><i></i></div>
  </div>
</footer>
<div class="copyright">© 2017 Company Name. All right reserved</div>

</body>
</html>
```